Mental Health care Company in Washington DC

We are a new mental health care services provider in Washington DC. Please look at these sites.
https://brightwaterfamilysupport.com
https://www.quietharborinc.com
https://willowgate-dc.org/
https://www.tidepathdc.com
https://www.thelanternofdc.com

```html
<!DOCTYPE html>
<html lang="en">
<head>
<meta charset="utf-8">
<title>Lumen Mind Services — Mental Health Care in Washington DC</title>
<link rel="stylesheet" href="https://fonts.googleapis.com/css2?family=Lora:ital,wght@0,400;0,500;1,400&family=Poppins:wght@300;400;500;600&display=swap">
<style>
:root{
  --orange:#f0914d;
  --orange-dark:#e07a34;
  --ink:#262626;
  --muted:#555;
  --line:#d9d9d9;
  --teal:#2d6f86;
  --footer:#121212;
  --white:#fff;
}
*{box-sizing:border-box;margin:0;padding:0}
html,body{width:1200px;height:4691px;overflow:hidden;background:#fff}
body{font-family:"Poppins",sans-serif;color:var(--ink);position:relative}
.abs{position:absolute}
.serif{font-family:"Lora",serif;font-weight:400}
.btn{position:absolute;background:var(--orange);color:#fff;font-size:13px;font-weight:600;letter-spacing:.5px;display:flex;align-items:center;justify-content:center;gap:14px;text-transform:uppercase;border-radius:2px}
.btn svg{width:32px;height:10px}
.rule{position:absolute;height:4px;background:var(--orange)}
.photo{position:absolute}

/* top bar + nav */
.topbar{position:absolute;left:0;top:0;width:1200px;height:40px}
.topbar .mail{position:absolute;left:570px;top:11px;font-size:14px;display:flex;gap:8px;align-items:center}
.topbar .phone{position:absolute;left:773px;top:0;width:180px;height:40px;background:var(--orange);color:#fff;font-weight:600;font-size:16px;display:flex;align-items:center;justify-content:center;gap:8px}
.social{position:absolute;width:26px;height:26px;border:1.5px solid #333;border-radius:50%}
.brand{position:absolute;left:110px;top:14px}
.brand .name{font-size:44px;font-weight:500;line-height:1;color:#333}
.brand .sub{font-size:15px;letter-spacing:9px;color:#888;margin-top:4px;padding-left:44px}
.brand .dot{position:absolute;left:48px;top:-6px;width:14px;height:14px;border-radius:50%;background:var(--orange)}
.nav{position:absolute;top:66px;font-size:13px;font-weight:500}
.nav.active{color:var(--orange)}
.navline{position:absolute;left:0;top:110px;width:1200px;height:1px;background:#e6e6e6}
.contact-btn{position:absolute;left:944px;top:52px;width:144px;height:46px;border:2px solid #555;font-size:15px;font-weight:500;display:flex;align-items:center;justify-content:center}

/* hero */
.hero{left:0;top:110px;width:1200px;height:680px;background:linear-gradient(180deg,#6a5a55 0%,#b48562 35%,#e8a15b 55%,#7c5a41 78%,#3a2a22 100%)}
.hero h1{position:absolute;left:90px;top:145px;font-size:50px;line-height:62px;color:#1f1f1f;font-family:"Lora",serif;font-weight:400}
.hero h1 em{font-style:italic}
.dots span{display:inline-block;width:12px;height:12px;border:1.5px solid #fff;border-radius:50%;margin-right:9px}
.dots .on{background:var(--orange);border-color:var(--orange)}

/* about */
.h2{position:absolute;font-family:"Lora",serif;font-size:48px;font-weight:400;color:#2a2a2a}
.about-copy{position:absolute;left:575px;top:888px;width:510px;display:flex;flex-direction:column;gap:12px}
.about-copy p{font-size:14.5px;line-height:27.5px;color:var(--muted);text-align:justify}
.about-copy .btn{position:static;width:176px;height:46px;margin-top:14px}
.para{position:absolute;font-size:16px;line-height:27.5px;color:var(--muted);text-align:justify}

/* services */
.services-bg{left:0;top:1660px;width:1200px;height:625px;background:linear-gradient(180deg,#fff 0%,#e9cdb3 30%,#d6a57c 70%,#ecdcc8 100%)}
.card{position:absolute;background:#fff;border-radius:16px;box-shadow:0 4px 14px rgba(0,0,0,.12);text-align:center}
.card h3{font-family:"Lora",serif;font-weight:400;font-size:18px;margin-top:132px}
.card p{font-size:11.5px;line-height:17px;color:#777;padding:0 20px;margin-top:14px}
.card .mini{position:absolute;left:69px;bottom:42px;width:110px;height:28px;background:var(--orange);color:#fff;font-size:9px;font-weight:600;display:flex;align-items:center;justify-content:center;gap:8px}
.card svg.icon{position:absolute;left:92px;top:38px;width:64px;height:64px}
.circle-btn{position:absolute;width:44px;height:44px;border-radius:50%;border:1.5px solid #fff;background:rgba(255,255,255,.35);display:flex;align-items:center;justify-content:center;font-size:18px}

/* testimonials */
.quote{position:absolute;width:450px;height:225px;background:#fff;border-radius:8px;box-shadow:0 4px 16px rgba(0,0,0,.12);padding:38px 14px 0}
.quote .t{font-size:16px;font-weight:500;color:#224a5a}
.quote .stars{position:absolute;right:18px;top:40px;color:var(--orange);font-size:17px;letter-spacing:3px}
.quote p{font-size:12.5px;line-height:21px;color:#444;text-align:center;margin-top:8px}
.quote .tail{position:absolute;left:88px;bottom:-22px;width:40px;height:40px;background:#fff;transform:rotate(45deg);box-shadow:6px 6px 8px rgba(0,0,0,.06)}
.person{position:absolute;display:flex;gap:16px;align-items:center}
.avatar{width:56px;height:56px;border-radius:50%;background:#bdb6b0;border:3px solid #fff;box-shadow:0 0 0 1.5px #999}
.person b{font-weight:500;font-size:16px;color:#224a5a;display:block}
.person span{font-size:14px;color:#224a5a}

/* blogs */
.blog-card{position:absolute;background:#fff;box-shadow:0 3px 12px rgba(0,0,0,.12)}
.meta{font-size:10.5px;color:#666;display:flex;gap:12px;align-items:center}
.meta i{display:inline-block;width:1px;height:14px;background:#555}
.blog-title{font-family:"Lora",serif;font-size:17px;line-height:20px;color:#222}
.blog-text{font-size:10.5px;line-height:16px;color:#555}

/* contact */
.contact-bg{left:0;top:3680px;width:1200px;height:620px;background:linear-gradient(180deg,#fff 0%,#f3efe8 40%,#c9ccb4 80%,#6f8450 100%)}
.form{position:absolute;left:157px;top:3755px;width:533px;height:445px;background:#fff}
.field{position:absolute;width:220px}
.field small{display:block;font-size:10.5px;color:#666}
.field div{font-size:12.5px;margin-top:3px;padding-bottom:8px;border-bottom:2px solid var(--teal)}
.info{position:absolute;left:690px;top:3755px;width:355px;height:445px;background:var(--orange);border-top-right-radius:34px;color:#fff}
.info .row{position:absolute;left:28px;display:flex;gap:18px;align-items:center;font-size:16px}
.info .row svg{width:30px;height:30px}

/* footer */
.footer{left:0;top:4300px;width:1200px;height:391px;background:var(--footer);color:#fff}
.fcol{position:absolute;top:82px}
.fcol h4{font-size:19px;font-weight:600}
.fcol .u{width:68px;height:3px;background:var(--orange);margin:10px 0 22px}
.fcol a{display:block;font-size:12.5px;color:#e6e6e6;line-height:26px;text-decoration:none}
</style>
</head>
<body>

<!-- Header -->
<header class="topbar">
  <div class="mail"><svg width="18" height="13" viewBox="0 0 18 13"><rect x="1" y="1" width="16" height="11" fill="none" stroke="#333" stroke-width="1.5"/><path d="M1 1l8 6 8-6" fill="none" stroke="#333" stroke-width="1.5"/></svg>info@lumenmind.com</div>
  <div class="phone"><svg width="16" height="16" viewBox="0 0 24 24"><path d="M6.6 10.8a15 15 0 006.6 6.6l2.2-2.2a1 1 0 011-.25 11.4 11.4 0 003.6.57 1 1 0 011 1V20a1 1 0 01-1 1A17 17 0 013 4a1 1 0 011-1h3.5a1 1 0 011 1c0 1.25.2 2.45.57 3.57a1 1 0 01-.25 1z" fill="#fff"/></svg>888.888.8888</div>
  <span class="social" style="left:978px;top:7px"></span>
  <span class="social" style="left:1016px;top:7px;background:#5fb3b5;border-color:#5fb3b5"></span>
  <span class="social" style="left:1054px;top:7px"></span>
</header>
<div class="brand"><span class="dot"></span><div class="name">Lumen Mind</div><div class="sub">SERVICES</div></div>
<nav>
  <span class="nav active" style="left:491px">Home</span>
  <span class="abs" style="left:500px;top:54px;width:14px;height:2px;background:var(--orange)"></span>
  <span class="nav" style="left:565px">About Us</span>
  <span class="nav" style="left:660px">Our Services</span>
  <span class="nav" style="left:776px">Blog</span>
  <span class="nav" style="left:841px">Testimonials</span>
</nav>
<a class="contact-btn">Contact Us</a>
<div class="navline"></div>

<!-- Hero -->
<section class="photo hero" role="img" aria-label="Woman sitting on a beach at sunset reading a book">
  <h1>Your Path to<br><em>Mental Wellness</em><br>Starts Here</h1>
  <div class="btn" style="left:90px;top:370px;width:176px;height:46px">Get Started</div>
  <div class="dots abs" style="left:90px;top:527px"><span></span><span></span><span class="on"></span><span></span></div>
</section>
<svg class="abs" style="left:0;top:640px" width="1200" height="160" viewBox="0 0 1200 160">
  <path d="M0 95 C220 20 420 40 600 90 C790 145 990 110 1200 40 L1200 160 L0 160Z" fill="#fff"/>
  <path d="M0 95 C150 45 320 30 470 62" fill="none" stroke="#f0914d" stroke-width="9"/>
  <path d="M700 140 C880 150 1050 110 1200 70" fill="none" stroke="#f0914d" stroke-width="9"/>
</svg>

<!-- About -->
<section>
  <h2 class="h2" style="left:112px;top:880px">About Us</h2>
  <div class="rule" style="left:112px;top:952px;width:120px"></div>
  <p class="serif abs" style="left:112px;top:985px;font-size:34px;line-height:47px;color:#2a2a2a">Supporting Washington<br>DC with compassionate,<br>personalized mental<br>health care.</p>
  <div class="about-copy">
    <p>Gaerspiciatis uncsecsde omnis istsee nata secseus erraseor sseit voluptatem accusantium doloremque laudan seftium, tsetam aseeem aperiam, eaque ipsa quae ab illo inventore veritatis et quasi architecto beatae vitae dicta sunt explicabo. Nemo enim ipsam voluptatem quia voluptas sit aspernatur aut odit aut fugit, sed quia consequuntur magni dolores eos qsequi.</p>
    <p>Kaoloremque laudan seftium, tsetam aseeem aperiam, eaque ipsa quae ab illo inventore veritatis et quasi architecto beatae vitae dicta sunt explicabo. Nemo enim ipsam voluptatem quia voluptas sit aspernatur aut odit aut fugit, sed quia consequuntur magni dolores eos qsequi.</p>
    <div class="btn">Learn More <svg viewBox="0 0 32 10"><path d="M0 5h30M25 1l5 4-5 4" stroke="#fff" fill="none" stroke-width="1.5"/></svg></div>
  </div>
  <div class="photo" role="img" aria-label="Support group seated in a circle in a bright room" style="left:112px;top:1208px;width:335px;height:382px;background:linear-gradient(135deg,#b9a58e,#6f6154 60%,#8b7a68)"></div>
  <div class="photo" role="img" aria-label="Therapist talking with a young client on a leather sofa" style="left:455px;top:1297px;width:630px;height:365px;background:linear-gradient(120deg,#8a8a84,#4f4640 45%,#7a4a32 80%,#3b3029);border-left:4px solid #fff;border-top:4px solid #fff"></div>
</section>

<!-- Services -->
<section>
  <div class="photo services-bg" role="img" aria-label="Soft blurred background of a person resting in warm light"></div>
  <h2 class="h2" style="left:38px;top:1820px">Our Services</h2>
  <p class="para" style="left:38px;top:1918px;width:290px;font-size:14px;line-height:24px;color:#3a3a3a;text-align:left">Kaoloremque laudascean seftium, tsetam aseeem aperiam, eaque ipsa quae ab illo inventore veritatis ecasec quasi architecto beatae vitae dicta susent explicabo. Nemo enim ipsam voluptatem quia voluptas sit aspernatur saecaut osdit au.</p>
  <div class="btn" style="left:38px;top:2093px;width:178px;height:46px">Learn More <svg viewBox="0 0 32 10"><path d="M0 5h30M25 1l5 4-5 4" stroke="#fff" fill="none" stroke-width="1.5"/></svg></div>
  <div class="circle-btn" style="left:241px;top:2094px">‹</div>
  <div class="circle-btn" style="left:295px;top:2094px">›</div>

  <div class="abs" style="left:622px;top:1790px;width:262px;height:350px;border:1.5px solid #8fc0c0;border-radius:18px"></div>
  <article class="card" style="left:355px;top:1802px;width:248px;height:363px">
    <svg class="icon" viewBox="0 0 64 64" fill="none" stroke="#222" stroke-width="2"><path d="M32 40c-10-7-16-12-16-19a8 8 0 0116-2 8 8 0 0116 2c0 7-6 12-16 19z"/><path d="M28 27h8M32 23v8" stroke="#f0914d"/><path d="M4 46l10 0 10 6h14a3 3 0 010 6H26M38 52l14-6a3 3 0 013 5L38 62H14"/></svg>
    <h3>Therapy &amp; Counseling</h3>
    <p>Faeed quia consequuntur magni dolores eos qui ratione voluptatem sequi nesciunt. Neque porro quisquam esest, qui dolorem ipsum quia dolor siseft amet, consectetur, adipisci velit, sed quia non numquam</p>
    <div class="mini">LEARN MORE <svg width="20" height="8"><path d="M0 4h18M14 1l4 3-4 3" stroke="#fff" fill="none"/></svg></div>
  </article>
  <article class="card" style="left:635px;top:1802px;width:248px;height:363px">
    <svg class="icon" viewBox="0 0 64 64" fill="none" stroke="#222" stroke-width="2"><path d="M22 60V48c-8-4-12-11-12-20a22 22 0 0144 0c0 4 2 7 4 10l-4 2v8h-8v12"/><circle cx="32" cy="28" r="7" stroke="#f0914d"/><path d="M32 16v4M32 36v4M20 28h4M40 28h4M24 20l3 3M37 33l3 3M24 36l3-3M37 23l3-3" stroke="#f0914d"/></svg>
    <h3>Psychiatric Evaluations</h3>
    <p>Faeed quia consequuntur magni dolores eos qui ratione voluptatem sequi nesciunt. Neque porro quisquam esest, qui dolorem ipsum quia dolor siseft amet, consectetur, adipisci velit, sed quia non numquam</p>
    <div class="mini">LEARN MORE <svg width="20" height="8"><path d="M0 4h18M14 1l4 3-4 3" stroke="#fff" fill="none"/></svg></div>
  </article>
  <article class="card" style="left:910px;top:1802px;width:248px;height:363px">
    <svg class="icon" viewBox="0 0 64 64" fill="none" stroke="#222" stroke-width="2"><path d="M14 30a18 18 0 0036 0M8 10v10h12M56 10v10H44M32 48v12M24 60h16"/><circle cx="8" cy="8" r="3"/><circle cx="56" cy="8" r="3"/><rect x="24" y="18" width="16" height="16" stroke="#f0914d"/><path d="M32 21v10M27 26h10" stroke="#f0914d"/></svg>
    <h3>Medication Management</h3>
    <p>Faeed quia consequuntur magni dolores eos qui ratione voluptatem sequi nesciunt. Neque porro quisquam esest, qui dolorem ipsum quia dolor siseft amet, consectetur, adipisci velit, sed quia non numquam</p>
    <div class="mini">LEARN MORE <svg width="20" height="8"><path d="M0 4h18M14 1l4 3-4 3" stroke="#fff" fill="none"/></svg></div>
  </article>
</section>

<!-- Testimonials -->
<section>
  <h2 class="h2" style="left:0;width:1200px;text-align:center;top:2388px">Testimonials</h2>
  <div class="rule" style="left:540px;top:2465px;width:120px"></div>
  <div class="quote" style="left:122px;top:2525px">
    <div class="t">Amazing Experience!</div><div class="stars">★★★★★</div>
    <p>"Karsp asedsdiciatis unde omnis iste natus error sisaeset voluptatem accusantium doloremque laudantium, totam rem aperiam, eaque ipsaes quae ab illo inventore veritatis eset quasaeseseasi architecto bascaes aseseatae vitae dicta sunt explicabo. Nemo esesnim ipsam voluptatem quia voluptas sit aspernatur asaut odseit aut fugitsed quia consequuntur."</p>
    <span class="tail"></span>
  </div>
  <div class="person" style="left:244px;top:2772px"><div class="avatar" role="img" aria-label="Client portrait"></div><div><b>Rowan Ellery</b><span>Lasei Ceasece, CEO</span></div></div>
  <div class="quote" style="left:624px;top:2525px">
    <div class="t">Amazing Experience!</div><div class="stars">★★★★★</div>
    <p>"Karsp asedsdiciatis unde omnis iste natus error sisaeset voluptatem accusantium doloremque laudantium, totam rem aperiam, eaque ipsaes quae ab illo inventore veritatis eset quasaeseseasi architecto bascaes aseseatae vitae dicta sunt explicabo. Nemo esesnim ipsam voluptatem quia voluptas sit aspernatur asaut odseit aut fugitsed quia consequuntur."</p>
    <span class="tail"></span>
  </div>
  <div class="person" style="left:746px;top:2772px"><div class="avatar" role="img" aria-label="Client portrait"></div><div><b>Rowan Ellery</b><span>Lasei Ceasece, CEO</span></div></div>
  <div class="abs" style="left:554px;top:2870px;display:flex;gap:12px">
    <span style="width:13px;height:13px;border:1.5px solid #777;border-radius:50%"></span>
    <span style="width:13px;height:13px;border:1.5px solid #7aaec0;background:#7aaec0;border-radius:50%"></span>
    <span style="width:13px;height:13px;border:1.5px solid #777;border-radius:50%"></span>
    <span style="width:13px;height:13px;border:1.5px solid #777;border-radius:50%"></span>
  </div>
</section>

<!-- Blogs -->
<section>
  <h2 class="h2" style="left:0;width:1200px;text-align:center;top:2955px">Latest Blogs</h2>
  <div class="rule" style="left:540px;top:3032px;width:120px"></div>
  <div class="photo" role="img" aria-label="Two women shaking hands in a counseling session" style="left:105px;top:3075px;width:468px;height:322px;background:linear-gradient(120deg,#dfe3e0,#a9b3ad 45%,#6e7f6a 80%,#52603f)"></div>
  <article class="blog-card" style="left:133px;top:3400px;width:490px;height:152px;padding:22px 34px">
    <div class="meta">◆ BY ADMIN <i></i> ▣ AUG 12, 2025</div>
    <div class="blog-title" style="font-size:20px;margin-top:14px">Perspiciatis unde omnis iste natus error sit.</div>
    <div class="blog-text" style="font-size:12px;line-height:20px;margin-top:8px">Saerspiciatis unde omnis iste natus error sit voluptatem accusan tium doloremque laudantiumotam rem aperiameaque.</div>
  </article>

  <article class="blog-card" style="left:642px;top:3075px;width:475px;height:128px">
    <div class="photo" role="img" aria-label="Adult daughter comforting elderly parent" style="left:4px;top:4px;width:166px;height:120px;background:linear-gradient(135deg,#b9a69a,#6c5a50)"></div>
    <div class="abs" style="left:188px;top:14px;width:260px">
      <div class="meta">◆ BY ADMIN <i></i> ▣ AUG 12, 2025</div>
      <div class="blog-title" style="margin-top:8px">Perspiciatis unde omnis iste natus error sit.</div>
      <div class="blog-text" style="margin-top:6px">Saerspiciatis unde omnis iste natus error sit voluptatem accusan tium.</div>
    </div>
  </article>
  <article class="blog-card" style="left:642px;top:3230px;width:475px;height:128px">
    <div class="photo" role="img" aria-label="Family gathered together at home" style="left:4px;top:4px;width:166px;height:120px;background:linear-gradient(135deg,#a07c62,#4a3528)"></div>
    <div class="abs" style="left:188px;top:14px;width:260px">
      <div class="meta">◆ BY ADMIN <i></i> ▣ AUG 12, 2025</div>
      <div class="blog-title" style="margin-top:8px">Perspiciatis unde omnis iste natus error sit.</div>
      <div class="blog-text" style="margin-top:6px">Saerspiciatis unde omnis iste natus error sit voluptatem accusan tium.</div>
    </div>
  </article>
  <article class="blog-card" style="left:642px;top:3380px;width:475px;height:128px">
    <div class="photo" role="img" aria-label="Woman sitting thoughtfully in a dim room" style="left:4px;top:4px;width:166px;height:120px;background:linear-gradient(135deg,#7c6e66,#3f3431 60%,#8a4f4f)"></div>
    <div class="abs" style="left:188px;top:14px;width:260px">
      <div class="meta">◆ BY ADMIN <i></i> ▣ AUG 12, 2025</div>
      <div class="blog-title" style="margin-top:8px">Perspiciatis unde omnis iste natus error sit.</div>
      <div class="blog-text" style="margin-top:6px">Saerspiciatis unde omnis iste natus error sit voluptatem accusan tium.</div>
    </div>
  </article>
  <div class="btn" style="left:521px;top:3585px;width:160px;height:46px">View All <svg viewBox="0 0 32 10"><path d="M0 5h30M25 1l5 4-5 4" stroke="#fff" fill="none" stroke-width="1.5"/></svg></div>
</section>

<!-- Contact -->
<section>
  <div class="photo contact-bg" role="img" aria-label="Soft focus grass and garden in morning light"></div>
  <div class="form">
    <h2 class="serif abs" style="left:18px;top:32px;font-size:34px">Get In Touch</h2>
    <div class="rule" style="left:18px;top:84px;width:62px;height:3px;background:var(--teal)"></div>
    <svg class="abs" style="left:464px;top:58px" width="46" height="26" viewBox="0 0 46 26" fill="none" stroke="#222" stroke-width="1.5"><rect x="14" y="2" width="30" height="22"/><path d="M14 2l15 12 15-12M0 8h10M4 14h8M0 20h10"/></svg>
    <div class="field" style="left:20px;top:120px"><small>Your Name</small><div>Daniel Carver</div></div>
    <div class="field" style="left:271px;top:120px"><small>Email Address</small><div>info.danielcarver.com</div></div>
    <div class="field" style="left:20px;top:197px"><small>Phone</small><div>888 888 8888</div></div>
    <div class="field" style="left:271px;top:197px"><small>Company</small><div>Northfield Co</div></div>
    <div class="field" style="left:20px;top:268px;width:400px"><small>Enter Message</small><div style="border:none">Hi, do you have a message to send?</div></div>
    <div class="abs" style="left:20px;top:387px;width:400px;height:2px;background:var(--teal)"></div>
    <div class="abs" style="left:438px;top:355px;width:66px;height:66px;border-radius:50%;background:#1d1d1d;display:flex;align-items:center;justify-content:center">
      <svg width="28" height="28" viewBox="0 0 24 24"><path d="M2 11l20-9-8 20-3-8z" fill="#fff"/></svg>
    </div>
  </div>
  <div class="info">
    <h2 class="serif abs" style="left:24px;top:32px;font-size:34px">Contact Us</h2>
    <div class="abs" style="left:24px;top:84px;width:62px;height:3px;background:#bfe0e0"></div>
    <svg class="abs" style="left:296px;top:64px" width="36" height="34" viewBox="0 0 36 34"><path d="M18 2L2 16h5v16h22V16h5z" fill="#fff"/><circle cx="18" cy="18" r="4" fill="#f0914d"/></svg>
    <div class="row" style="top:135px;font-size:12.5px;line-height:20px"><svg viewBox="0 0 30 30" fill="none" stroke="#fff" stroke-width="1.5"><path d="M15 26s9-8 9-15a9 9 0 00-18 0c0 7 9 15 9 15z"/><circle cx="15" cy="11" r="3"/></svg><span>1180 Maple Row Lane, Washington,<br>DC 20001</span></div>
    <div class="row" style="top:210px"><svg viewBox="0 0 30 30" fill="none" stroke="#fff" stroke-width="1.5"><rect x="4" y="3" width="10" height="24" rx="2"/><rect x="17" y="7" width="10" height="20"/><path d="M19 11h6M19 15h6M19 19h6"/></svg><span>888.888.8888</span></div>
    <div class="row" style="top:276px"><svg viewBox="0 0 30 30" fill="none" stroke="#fff" stroke-width="1.5"><path d="M3 12l12-9 12 9v15H3z"/><path d="M3 12l12 8 12-8"/></svg><span>info@lumenmind.com</span></div>
    <span class="abs" style="left:32px;top:362px;width:28px;height:28px;border:1.5px solid #fff;border-radius:50%"></span>
    <span class="abs" style="left:74px;top:362px;width:28px;height:28px;background:#fff;border-radius:50%"></span>
    <span class="abs" style="left:116px;top:362px;width:28px;height:28px;border:1.5px solid #fff;border-radius:50%"></span>
  </div>
</section>

<!-- Footer -->
<footer class="abs footer">
  <div class="abs" style="left:143px;top:108px">
    <span class="abs" style="left:48px;top:-12px;width:14px;height:14px;border-radius:50%;background:var(--orange)"></span>
    <div style="font-size:44px;font-weight:500;line-height:1">Lumen Mind</div>
    <div style="font-size:15px;letter-spacing:9px;color:#ccc;margin-top:6px;padding-left:44px">SERVICES</div>
  </div>
  <div class="fcol" style="left:487px"><h4>Quick links</h4><div class="u"></div><a>Home</a><a>About</a><a>Services</a><a>Blog</a><a>Contact Us</a></div>
  <div class="fcol" style="left:697px"><h4>Links</h4><div class="u"></div><a>Copyright</a><a>Legal</a><a>Privacy</a><a>Accessibility</a><a>Sitemap</a></div>
  <div class="fcol" style="left:886px"><h4>Support</h4><div class="u"></div><a>FAQs</a><a>Privacy Policy</a><a>Terms of Service</a><a>Request a Quote</a><a>Client Login</a></div>
  <svg class="abs" style="left:1130px;top:280px" width="16" height="48" viewBox="0 0 16 48"><path d="M8 48V2M2 9l6-7 6 7" fill="none" stroke="#fff" stroke-width="1.5"/></svg>
  <div class="abs" style="left:110px;top:330px;width:1000px;height:1px;background:#333"></div>
  <div class="abs" style="left:110px;top:352px;font-size:12px;color:#ddd">Copyright ©2025. All Rights Reserved</div>
  <div class="abs" style="left:861px;top:352px;font-size:12px;color:#ddd">Terms of use</div>
  <div class="abs" style="left:971px;top:352px;font-size:12px;color:#ddd">Privacy Policy</div>
</footer>

</body>
</html>
```